card for handyman and landscaping business, double sided with services listed on the back

Design a business card for a handyman and Landscaping business in San Jose,ca. Would like front to be a house with 3D characters doing different tasks i.e. Mowing lawn, painting, sprinklers, lighting, weed whacking, power washing, lumber etc. on the backside a cutout of the interior with computer, internet, cleaning, bathroom/kitchen remodeling, smart home etc.

Industry/Entity Type

Handyman

Contact Information for Business Card

Two sided view of a house, one outside services and one inside services

Colors

Designer to choose colors to be used in the design.

Requirements
Must have
• General Household Repairs and Maintenance
• Landscaping, Gardening, and Planting
• Painting, Patching and Trim/Moulding Work
• Cleaning, Restoring and Hauling/Trash Removal
• Blinds, Curtains, and Assembly Work
• Computer, Internet/Wireless, and Smart Home Service

```html
<!DOCTYPE html>
<html lang="en">
<head>
<meta charset="utf-8">
<title>Handyman Landscaping and Tech Services – Business Card</title>
<link rel="stylesheet" href="https://fonts.googleapis.com/css2?family=Oswald:wght@700&family=Source+Sans+3:wght@400;600;700&display=swap">
<style>
  :root {
    --stage: #1b1b1b;
    --paper: #f1f1f1;
    --green: #339e4d;
    --green-dark: #0f4f27;
    --ink: #1d1d1d;
    --white: #ffffff;
  }
  html, body { margin: 0; padding: 0; overflow: hidden; }
  body { width: 1200px; height: 900px; background: var(--stage); position: relative; font-family: "Source Sans 3", "Myriad Pro", sans-serif; }
  .card { position: absolute; top: 170px; width: 347px; height: 561px; background: var(--paper); overflow: hidden; }
  .card--front { left: 259px; }
  .card--back { left: 631px; }
  .house-band { position: absolute; left: 0; top: 0; width: 347px; height: 561px; }
  .company-name { position: absolute; top: 40px; left: 0; width: 100%; margin: 0; text-align: center; font-family: "Oswald", "Impact", sans-serif; font-weight: 700; font-size: 28px; line-height: 36px; letter-spacing: 0.6px; color: var(--green-dark); transform: scaleX(0.92); }
  .contact { position: absolute; top: 134px; left: 0; width: 100%; text-align: center; color: var(--ink); }
  .contact__name { margin: 0; font-size: 19.5px; font-weight: 600; color: var(--green-dark); line-height: 22px; letter-spacing: 0.3px; }
  .contact__role { margin: 0 0 9px; font-size: 15.5px; line-height: 18px; }
  .contact__line { margin: 0; font-size: 15.5px; line-height: 20.5px; }
  .contact__label { color: var(--green-dark); font-weight: 700; }
  .contact__web { margin: 0 0 8px; font-size: 15.5px; line-height: 20.5px; font-weight: 700; color: var(--green-dark); }
  .contact__address { margin: 0; font-size: 15.5px; line-height: 20.5px; }
  .services-title { position: absolute; top: 54px; left: 0; width: 100%; margin: 0; text-align: center; font-family: "Oswald", "Impact", sans-serif; font-weight: 700; font-size: 28px; line-height: 36px; color: var(--green-dark); transform: scaleX(0.92); }
  .services-list { position: absolute; top: 122px; left: 0; width: 100%; margin: 0; padding: 0; list-style: none; text-align: center; font-size: 14.2px; line-height: 25.2px; color: var(--ink); }
  .services-list .sep { color: var(--green); padding: 0 4px; }
  .icon-badge { position: absolute; width: 64px; height: 64px; border-radius: 50%; background: var(--white); }
  .icon-badge svg { width: 64px; height: 64px; display: block; fill: var(--green-dark); stroke: var(--green-dark); }
</style>
</head>
<body>

<section class="card card--front" aria-label="Card front">
  <svg class="house-band" viewBox="0 0 347 561" aria-hidden="true">
    <path d="M0 358 H189 L249 308 L310 358 H347 V561 H0 Z" fill="var(--green)"/>
    <path d="M0 360 H189 L249 310 L310 360 H347" fill="none" stroke="var(--green-dark)" stroke-width="6"/>
    <g fill="var(--white)"><rect x="242" y="343" width="6.5" height="6.5"/><rect x="250.5" y="343" width="6.5" height="6.5"/><rect x="242" y="351.5" width="6.5" height="6.5"/><rect x="250.5" y="351.5" width="6.5" height="6.5"/></g>
  </svg>

  <h1 class="company-name">HANDYMAN&nbsp; LANDSCAPING<br>AND TECH SERVICES</h1>

  <div class="contact">
    <p class="contact__name">DANIEL REYES</p>
    <p class="contact__role">Managing Director</p>
    <p class="contact__line"><span class="contact__label">P:</span> (044)555018274</p>
    <p class="contact__line"><span class="contact__label">E:</span> hello@reyeshomepro.com</p>
    <p class="contact__web">www.reyeshomepro.com</p>
    <p class="contact__address">4820, Alder Grove Lane,<br>San Jose CA, 95123</p>
  </div>

  <div class="icon-badge" style="left:56px;top:388px" aria-label="Bathroom">
    <svg viewBox="0 0 64 64"><rect x="20" y="16" width="24" height="13" rx="2" stroke="none"/><path d="M18 32 H46 C46 40 40 44 36 44 V50 H28 V44 C24 44 18 40 18 32Z" stroke="none"/></svg>
  </div>
  <div class="icon-badge" style="left:140px;top:388px" aria-label="Cleaning">
    <svg viewBox="0 0 64 64"><path d="M44 16 L33 34" stroke-width="3" fill="none"/><path d="M33 32 C26 30 18 36 16 46 C24 48 34 44 38 36Z" stroke="none"/><circle cx="44" cy="46" r="2" stroke="none"/><circle cx="40" cy="49" r="1.5" stroke="none"/></svg>
  </div>
  <div class="icon-badge" style="left:225px;top:388px" aria-label="Computer and internet">
    <svg viewBox="0 0 64 64"><rect x="16" y="17" width="32" height="22" rx="2" stroke="none"/><path d="M26 28 Q32 22 38 28 M29 31 Q32 28 35 31" stroke="#fff" stroke-width="2" fill="none"/><rect x="18" y="42" width="28" height="6" rx="1" stroke="none"/></svg>
  </div>
  <div class="icon-badge" style="left:56px;top:473px" aria-label="Wireless">
    <svg viewBox="0 0 64 64"><path d="M32 30 L26 48 H38Z" stroke="none"/><circle cx="32" cy="29" r="3" stroke="none"/><path d="M24 22 Q19 29 24 36 M40 22 Q45 29 40 36 M19 18 Q12 29 19 40 M45 18 Q52 29 45 40" fill="none" stroke-width="2.5"/></svg>
  </div>
  <div class="icon-badge" style="left:140px;top:473px" aria-label="Lighting">
    <svg viewBox="0 0 64 64"><circle cx="32" cy="30" r="9" stroke="none"/><rect x="28" y="38" width="8" height="8" rx="1" stroke="none"/><path d="M32 14 V18 M20 19 L23 22 M44 19 L41 22 M16 30 H20 M44 30 H48" stroke-width="2.5" fill="none"/></svg>
  </div>
  <div class="icon-badge" style="left:225px;top:473px" aria-label="Smart home">
    <svg viewBox="0 0 64 64"><path d="M14 32 L32 16 L50 32 H45 V48 H19 V32Z" stroke="none"/><circle cx="32" cy="37" r="6" fill="none" stroke="#fff" stroke-width="2"/><path d="M32 30 V36" stroke="#fff" stroke-width="2"/></svg>
  </div>
</section>

<section class="card card--back" aria-label="Card back">
  <svg class="house-band" viewBox="0 0 347 561" aria-hidden="true">
    <path d="M0 358 H189 L249 308 L310 358 H347 V561 H0 Z" fill="var(--green)"/>
    <path d="M0 360 H189 L249 310 L310 360 H347" fill="none" stroke="var(--green-dark)" stroke-width="6"/>
    <g fill="var(--white)"><rect x="242" y="343" width="6.5" height="6.5"/><rect x="250.5" y="343" width="6.5" height="6.5"/><rect x="242" y="351.5" width="6.5" height="6.5"/><rect x="250.5" y="351.5" width="6.5" height="6.5"/></g>
  </svg>

  <h2 class="services-title">SERVICES</h2>

  <ul class="services-list">
    <li>Handyman<span class="sep">|</span>Landscaping<span class="sep">|</span>Sprinklers/Irrigation</li>
    <li>Painting<span class="sep">|</span>Electrical<span class="sep">|</span>Lighting</li>
    <li>Power Washing<span class="sep">|</span>Hauling<span class="sep">|</span>Cleaning</li>
    <li>Bath/Kitchen<span class="sep">|</span>Baseboards/Trim/Moulding</li>
    <li>Smart Home<span class="sep">|</span>A/C and Heating<span class="sep">|</span>Blinds, Curtains</li>
    <li>Assembly Services<span class="sep">|</span>Computer/Tech Service</li>
  </ul>

  <div class="icon-badge" style="left:55px;top:394px" aria-label="Lawn mowing">
    <svg viewBox="0 0 64 64"><path d="M12 20 L30 34" stroke-width="3" fill="none"/><path d="M26 32 H46 L50 42 H24Z" stroke="none"/><circle cx="28" cy="44" r="4" stroke="none"/><circle cx="46" cy="44" r="4" stroke="none"/></svg>
  </div>
  <div class="icon-badge" style="left:139px;top:394px" aria-label="Painting trim">
    <svg viewBox="0 0 64 64"><rect x="18" y="34" width="28" height="5" stroke="none"/><path d="M26 16 L34 14 L38 26 L30 28Z" stroke="none"/><path d="M34 27 L40 46" stroke-width="3" fill="none"/></svg>
  </div>
  <div class="icon-badge" style="left:223px;top:394px" aria-label="Paint roller">
    <svg viewBox="0 0 64 64"><rect x="18" y="16" width="26" height="11" rx="2" stroke="none"/><path d="M44 21 H48 V32 H32 V38" fill="none" stroke-width="2.5"/><rect x="29" y="38" width="6" height="12" rx="1" stroke="none"/></svg>
  </div>
  <div class="icon-badge" style="left:55px;top:471px" aria-label="Power washing">
    <svg viewBox="0 0 64 64"><path d="M14 30 H40 V35 H26 L22 46 H16 L19 35 H14Z" stroke="none"/><path d="M42 32 L52 27 M42 32 L52 32 M42 32 L52 37" stroke-width="1.5" fill="none"/></svg>
  </div>
  <div class="icon-badge" style="left:139px;top:471px" aria-label="Hauling and trash removal">
    <svg viewBox="0 0 64 64"><path d="M20 18 H44 L41 48 H23Z" stroke="none"/><rect x="22" y="21" width="20" height="3" fill="#fff" stroke="none"/><circle cx="25" cy="44" r="4" fill="#fff" stroke="none"/><circle cx="25" cy="44" r="2.5" stroke="none"/></svg>
  </div>
  <div class="icon-badge" style="left:223px;top:471px" aria-label="Windows and blinds">
    <svg viewBox="0 0 64 64"><rect x="17" y="17" width="30" height="30" fill="none" stroke-width="4"/><path d="M32 17 V47 M17 32 H47" stroke-width="3.5"/></svg>
  </div>
</section>

</body>
</html>
```